Cover für den Roman Hanna betritt die Leinwand
Zielgruppe
Autorin einer belletristischen Erzählung über die Kunst der Moderne. Das Buch richtet sich an Leser die sich für Moderne Kunst interessieren.
Aufgabenstellung
Gesucht wird ein sehr zeitgemäßes und auffallendes Design, auch gerne mit einer starken Hintergrundfarbe. Der Leser soll auf den ersten Blick erkennen können, dass es hier um Kunst geht (Odo Marquet, Drosanow, Veluzzi Ferrant, etc). Bitte unbedingt alle Lizenzrechte abklären und keine Originalwerke verwenden.
Eine Idee wäre einen Bezug zu "Hanna und der Barakleon" herzustellen. (Vielzitiertes Thema in der Kunstgeschichte, Hanna schlägt dem Feldherrn Barakleon den Kopf ab und befreit ihr Volk.)
Das Design sollte aber trotzdem nett und nicht gruselig sein.
Ganz wichtig keine nackte Hanna. Sie ist stark und emanzipiert sich!
Text auf der Vorderseite:
Wiebke Talhammer
Hanna betritt die Leinwand
Erzählung über die Kunst der Moderne
Text auf der Rückseite:
kurze Inhaltsangabe
Das Cover soll für ein Taschenbuch als auch ein e-book funktionieren

```html
<!DOCTYPE html>
<html lang="de">
<head>
<meta charset="utf-8">
<title>Hanna betritt die Leinwand – Cover</title>
<link rel="stylesheet" href="https://fonts.googleapis.com/css2?family=Parisienne&family=Alegreya+Sans+SC:wght@500&family=Cutive&family=Spectral:wght@400&display=swap">
<style>
  :root {
    --canvas-w: 912px;
    --canvas-h: 1200px;
    --ink-dark: #2d2a22;
    --band-green: rgba(196, 208, 160, 0.82);
    --title-orange: #e07a26;
    --title-green: #6e8d3a;
    --glow-white: rgba(255, 250, 235, 0.95);
    --glow-orange: #c8601e;
    --paint-cream: #f3e4c2;
    --paint-ochre: #e9a640;
    --paint-rust: #b4471d;
    --paint-dark: #2a1d14;
    --paint-blue: #2f8fc0;
    --paint-teal: #1f6f7a;
    --paint-sand: #d9b27a;
  }
  * { margin: 0; padding: 0; box-sizing: border-box; }
  html, body { width: var(--canvas-w); height: var(--canvas-h); overflow: hidden; background: #fff; }
  .cover {
    position: relative;
    width: var(--canvas-w);
    height: var(--canvas-h);
    overflow: hidden;
  }
  .cover-artwork {
    position: absolute;
    inset: 0;
    background:
      radial-gradient(ellipse 38% 30% at 58% 38%, var(--paint-cream) 0%, rgba(243,228,194,0) 100%),
      radial-gradient(ellipse 40% 35% at 55% 12%, var(--paint-ochre) 0%, rgba(233,166,64,0) 100%),
      radial-gradient(ellipse 35% 40% at 92% 70%, var(--paint-blue) 0%, rgba(47,143,192,0) 100%),
      radial-gradient(ellipse 30% 30% at 95% 28%, var(--paint-teal) 0%, rgba(31,111,122,0) 100%),
      radial-gradient(ellipse 45% 35% at 20% 85%, var(--paint-rust) 0%, rgba(180,71,29,0) 100%),
      radial-gradient(ellipse 30% 45% at 6% 35%, var(--paint-dark) 0%, rgba(42,29,20,0) 100%),
      radial-gradient(ellipse 40% 25% at 60% 95%, var(--paint-dark) 0%, rgba(42,29,20,0) 100%),
      linear-gradient(160deg, var(--paint-sand) 0%, var(--paint-ochre) 45%, var(--paint-rust) 100%);
  }
  .author-band {
    position: absolute;
    left: 0;
    top: 50px;
    width: 100%;
    height: 84px;
    background: var(--band-green);
    display: flex;
    align-items: center;
    justify-content: center;
  }
  .author-name {
    font-family: "Spectral", serif;
    font-size: 46px;
    color: var(--ink-dark);
    letter-spacing: 1px;
  }
  .title-name {
    position: absolute;
    left: 80px;
    top: 430px;
    font-family: "Parisienne", cursive;
    font-size: 210px;
    line-height: 1;
    color: var(--title-orange);
    text-shadow: 0 0 6px rgba(255,240,210,0.6);
  }
  .title-rest {
    position: absolute;
    left: 310px;
    top: 655px;
    font-family: "Alegreya Sans SC", sans-serif;
    font-weight: 500;
    color: var(--title-green);
    line-height: 1.25;
    text-shadow: 0 0 6px var(--glow-white), 0 0 12px var(--glow-white);
  }
  .title-rest .line-1 { display: block; font-size: 62px; letter-spacing: 4px; }
  .title-rest .line-2 { display: block; font-size: 64px; letter-spacing: 1px; }
  .subtitle {
    position: absolute;
    right: 32px;
    top: 930px;
    font-family: "Cutive", serif;
    font-size: 50px;
    line-height: 1.6;
    color: #fffaf0;
    text-align: center;
    text-shadow: 0 0 4px var(--glow-orange), 0 0 10px var(--glow-orange);
  }
</style>
</head>
<body>
  <main class="cover">
    <div class="cover-artwork" role="img" aria-label="Abstraktes Gemälde eines Frauengesichts in Ocker, Creme, Rostrot und Blau im Stil der Moderne"></div>

    <header class="author-band">
      <p class="author-name">Wiebke Talhammer</p>
    </header>

    <h1 class="book-title">
      <span class="title-name">Hanna</span>
      <span class="title-rest">
        <span class="line-1">betritt die</span>
        <span class="line-2">Leinwand</span>
      </span>
    </h1>

    <p class="subtitle">Erzählung über die<br>Kunst der Moderne</p>
  </main>
</body>
</html>
```